Website development company website

ABOUT COMPANY
Hi everyone! We're a Melbourne, Australia website development company in a need of a website design that will make online store merchants want to engage our services.
We specialise exclusively in Torvista e-commerce platform (https://torvista-platform.example/). What distinguishes our business from competition is that rather than designing and building brand new websites, we offer development, support and maintenance services to established websites. Maintenance and Support are the keywords representing our business.
Our potential clients are people with broken, slow and underperforming Torvista installations who need assistance getting their websites up and making sales. Our website must pass the message that we can help, and provide quick means of making contact.
DESIGN
Overall, we're looking for a slick, clean, airy, conservative design. No need to do anything crazy, try to stick to what's "standard" in website design these days and make it easy on all of us. The website is unlikely to be updated too often so it needs to look attractive and fresh first time over and after a year, too.
Attached is our new logo, which you'll be able to take the basic idea from, the colors and fonts. Though, don't use the fonts from the logo in the website, stick to the standard widely supported fonts. Additional use of Google fonts is fine.
Don't overdo it with colors, stick to conservative basic color set and only use the colors from the log for accents like headings etc. Please, don't be tempted to use the blue and orange as background of whole blocks, other than perhaps footer. Thanks.
For the images used, I'd like to stay away from a design studio/digital agency feel and lean more towards professional support and maintenance services. I'm thinking images of content merchants doing their job. Something along the lines of "We'll be taking care of the website so that you only need to care about the business".
Some ideas I like:
http://www.plumframe-pics.example/detail/photo/portrait-of-confident-male-design-professional-royalty-free-image/572048163
http://www.plumframe-pics.example/detail/photo/designer-taking-picture-of-hat-high-res-stock-photography/839207514
http://www.plumframe-pics.example/detail/photo/woman-packaging-pottery-royalty-free-image/216684093
Images of colorful shopping bags and shopping carts are over the top and not serious enough. Instead of images matching Online Shopping, I'd try going more for Stability, Reliability, Performance.
Our existing website is http://www.bravuln.example. Please, don't take design ideas from it, but it will give you a picture of the structure of our new website and content that's going to be used initially.
If you could include a basic icon set to use throughout the website, that would be great. If the icons could match our logo (attached), it would be a big plus.
ALL PAGES
Every page must contain clearly visible phone number (1300 648 907) and a Contact Us Now button, which opens an AJAX driven popup form with Name, Email, Phone and Message to be sent through.
To start with, main menu items will be Torvista, Portfolio, Contact.
At the bottom of each page, please, include a newsletter subscription form with text Subscribe to Torvista Support and Security Updates.
For the footer, I'd like to see a logo strip with the following logos in grayscale (no need to link anywhere): Torvista, QRX, DataVane, NCB. You'll find the logos on Google Images.
Standard footer columns follow. Here, I'd like to see logos in color: Torvista Certified Developer, Torvista Ceritified Solution Provider. Again, the logos are on Google Images.
No social media logos/links necessary anywhere on the website.
...and then the copyright line.
FRONT PAGE
Large slider with images that would appeal to our target audience. Keywords here would be Torvista System Audit, Torvista Performance Optimisation, Torvista Website Emergency Recovery, Torvista Development Infrastructure Hosting. We'll have a static page created for each of these to link to.
In a corner of the slider, or on the edge, can I have an overlay with logos in color (same as footer): Torvista Certified Developer, Torvista Ceritified Solution Provider.
Underneath, a number of blocks, each with an image and teaser that we'll use to link to various pages throughout the website.
PORTFOLIO PAGE
I'm thinking a single long page with a block per client, which will contain project name, description from us and a testimonial from client. Also, each block will contain a single large screenshot. No gallery or slideshow is necessary here, just one image per project.
I'll leave the layout up to you, but try to put yourself in the shoes of a potential client reviewing our past work by simply scrolling down this one page.
CONTACT US PAGE
Separate page with the same form as above, phone number (1300 648 907), email address (support@kavreo.example), address (Suite 42, Level 3|8 Wattlebrook Lane|Fernvale Heights VIC 3999), and a grayscale Google Map.
CODING UP
Coding up into static HTML/CSS/JS is equally important as the design itself. We're a website development company, we'll be integrating the theme. We will spot any issues and we will point them out.
Coded up design must be fully responsive. Enough said.
To be able to create any content in future, we'd like one extra page coded up with samples of all themed elements, lists, forms, buttons, 2, 3, 4-column layout, alerts, icons, etc. This page does not need to be designed, only coded up.
The design will be integrated into Drupal using Twig. If possible at all, try to keep it in mind when designing and coding up, and make the integration into a Drupal theme easier for us.
GOOD LUCK!
That's it. Let me know if anything needs clarifying. So far I've had a great experience with ArtFlockly. I don't doubt some great designs will emerge. Clever ideas are highly appreciated, but also make it clear you've read and followed the points in this brief. Cheers, Tom

```html
<!DOCTYPE html>
<html lang="en">
<head>
<meta charset="utf-8">
<title>Kavreo E-Commerce</title>
<link rel="stylesheet" href="https://fonts.googleapis.com/css2?family=Open+Sans:wght@300;400;600;700&family=Roboto+Condensed:wght@700&display=swap">
<style>
:root{
  --blue:#0f3a6b;
  --orange:#e57c22;
  --text:#555b60;
  --band:#ebebeb;
  --rule:#cfcfcf;
  --dark:#1f2224;
  --white:#ffffff;
  --hero-light:#f4f6f8;
  --hero-window:#dfe6ec;
  --hero-warm:#c9b8a6;
  --hero-desk:#d8d2ca;
}
*{box-sizing:border-box;margin:0;padding:0}
html,body{width:1200px;height:2632px;overflow:hidden}
body{position:relative;background:var(--white);font-family:"Open Sans",Arial,sans-serif;color:var(--text)}
.abs{position:absolute}

.hero{left:0;top:0;width:1200px;height:798px;
  background:
    linear-gradient(180deg,rgba(255,255,255,0) 0%,rgba(255,255,255,0) 86%,rgba(226,220,212,.95) 91%,rgba(236,232,226,1) 100%),
    radial-gradient(ellipse 190px 150px at 935px 210px,rgba(110,78,56,.55) 0%,rgba(110,78,56,0) 100%),
    radial-gradient(ellipse 230px 330px at 1030px 520px,rgba(250,250,250,.95) 0%,rgba(250,250,250,0) 100%),
    radial-gradient(ellipse 300px 200px at 700px 610px,rgba(214,208,200,.9) 0%,rgba(214,208,200,0) 100%),
    linear-gradient(90deg,var(--hero-window) 0%,var(--hero-light) 9%,#c9d3dc 14%,var(--hero-light) 22%,#e9eef2 34%,#d4dce3 40%,var(--hero-light) 52%,#e3e4e4 64%,var(--hero-warm) 80%,#e6e2dc 92%,var(--hero-light) 100%)}
.hero-brand{left:400px;top:352px;width:420px;text-align:center;color:var(--blue);
  font-weight:700;font-size:78px;line-height:1;letter-spacing:-1px}
.hero-brand small{display:block;font-size:24px;font-weight:700;letter-spacing:3px;margin-top:10px}

.main-nav{left:0;top:798px;width:1200px;height:62px;background:var(--blue)}
.main-nav a{position:absolute;top:0;line-height:62px;color:var(--white);font-size:19px;text-decoration:none;text-transform:uppercase}
.main-nav a.is-active{color:var(--orange)}
.nav-phone{position:absolute;left:882px;top:0;width:318px;height:62px;background:var(--orange);
  color:var(--white);font-family:"Roboto Condensed",Arial,sans-serif;font-weight:700;font-size:27px;
  display:flex;align-items:center;justify-content:center;gap:8px}

.section-title{font-weight:300;font-size:41px;text-align:center;text-transform:uppercase;color:var(--blue);letter-spacing:.5px}
.section-title .accent{color:var(--orange)}
.body-text{font-size:15.5px;line-height:25px}

.intro-title{left:0;top:905px;width:1200px}
.intro-text{left:168px;top:970px;width:864px;text-align:center}

.service{top:1078px;width:320px;text-align:center}
.service svg{display:block;margin:0 auto}
.service h3{font-weight:400;font-size:27px;color:var(--blue);margin-top:16px;margin-bottom:8px}

.why-band{left:0;top:1316px;width:1200px;height:333px;background:var(--band)}
.why h2{position:absolute;top:1366px;font-weight:400;font-size:28px;color:var(--blue);text-transform:uppercase;white-space:nowrap}
.why-mark{position:absolute;top:1482px;width:140px;text-align:center;font-weight:600;font-size:26px;color:var(--blue)}
.why-rule{position:absolute;top:1421px;width:1px;height:168px;background:var(--rule)}
.why-text{position:absolute;top:1426px;width:310px}
.btn{position:absolute;display:block;height:49px;line-height:49px;background:var(--orange);color:var(--white);
  text-align:center;font-size:21px;text-transform:uppercase;text-decoration:none}

.work-title{left:0;top:1686px;width:1200px}
.work-card{top:1759px;width:234px}
.work-thumb{height:135px;border:1px solid #cfcfcf;display:flex;align-items:center;justify-content:center;
  font-weight:600;font-size:26px;color:var(--blue)}
.work-card h4{font-weight:400;font-size:22px;color:var(--blue);margin-top:16px}
.work-card p{margin-top:6px}
.work-card cite{display:block;font-style:normal;color:var(--orange);font-size:15.5px;margin-top:4px}

.newsletter{left:0;top:2201px;width:1200px;height:251px;
  background:linear-gradient(90deg,#2a2c2e 0%,#1b1d1f 45%,#2e2f30 75%,#1a1b1c 100%)}
.newsletter-title{left:0;top:2245px;width:1200px;text-align:center;font-weight:300;font-size:41px;color:var(--orange)}
.newsletter-sub{left:0;top:2300px;width:1200px;text-align:center;color:var(--white);font-size:18px}
.field{position:absolute;top:2350px;height:46px;width:332px;border:1px solid #4a4c4e;background:#1c1e20;
  color:var(--white);font-size:15px;line-height:44px;padding-left:16px}
.btn-subscribe{left:870px;top:2350px;width:167px;height:46px;line-height:46px;font-size:21px}

.partner{position:absolute;top:2508px;width:200px;text-align:center;font-weight:600;font-size:32px;color:#8d8d8d}
.copyright{left:0;top:2590px;width:1200px;text-align:center;font-size:14px;color:#666}
.copyright strong{color:var(--blue);font-weight:600}
</style>
</head>
<body>

<div class="abs hero" role="img" aria-label="Bright office photo of a smiling businesswoman in a white jacket working at a laptop on a desk"></div>
<div class="abs hero-brand">Kavreo<small>E-COMMERCE</small></div>

<nav class="abs main-nav">
  <a class="is-active" href="#" style="left:81px">Home</a>
  <a href="#" style="left:202px">About</a>
  <a href="#" style="left:333px">Torvista</a>
  <a href="#" style="left:491px">Portfolio</a>
  <a href="#" style="left:660px">Contact</a>
  <div class="nav-phone">
    <svg width="24" height="24" viewBox="0 0 24 24" aria-hidden="true"><path fill="#fff" d="M6.6 10.8a15.1 15.1 0 0 0 6.6 6.6l2.2-2.2a1 1 0 0 1 1-.25 11.4 11.4 0 0 0 3.6.57 1 1 0 0 1 1 1V20a1 1 0 0 1-1 1A17 17 0 0 1 3 4a1 1 0 0 1 1-1h3.5a1 1 0 0 1 1 1c0 1.25.2 2.45.57 3.57a1 1 0 0 1-.25 1z"/></svg>
    1300 648 907
  </div>
</nav>

<h1 class="abs section-title intro-title"><span class="accent">Welcome to</span> Kavreo E-Commerce</h1>
<p class="abs body-text intro-text">Lorem Ipsum is simply dummy text of the printing and typesetting industry. Lorem Ipsum has been the industry's standard dummy text ever since the 1500s, when an unknown printer took a galley of type and scrambled it to make a type specimen book.</p>

<div class="abs service" style="left:72px">
  <svg width="56" height="56" viewBox="0 0 56 56" aria-hidden="true"><path d="M20 16 8 28l12 12M36 16l12 12-12 12M31 12l-6 32" fill="none" stroke="#e57c22" stroke-width="5" stroke-linecap="round" stroke-linejoin="round"/></svg>
  <h3>DEVELOPMENT</h3>
  <p class="body-text">Lorem Ipsum is simply dummy text of the printing and typesetting industry. Lorem Ipsum has been the industry.</p>
</div>
<div class="abs service" style="left:438px">
  <svg width="56" height="56" viewBox="0 0 56 56" aria-hidden="true"><path d="M14 30v-6a14 14 0 0 1 28 0v6" fill="none" stroke="#e57c22" stroke-width="4"/><rect x="10" y="26" width="8" height="12" rx="3" fill="#e57c22"/><rect x="38" y="26" width="8" height="12" rx="3" fill="#e57c22"/><path d="M12 54a16 12 0 0 1 32 0z" fill="#e57c22"/></svg>
  <h3>SUPPORT</h3>
  <p class="body-text">Lorem Ipsum is simply dummy text of the printing and typesetting industry. Lorem Ipsum has been the industry.</p>
</div>
<div class="abs service" style="left:806px">
  <svg width="56" height="56" viewBox="0 0 56 56" aria-hidden="true"><circle cx="22" cy="32" r="11" fill="none" stroke="#e57c22" stroke-width="9" stroke-dasharray="5 3.6"/><circle cx="22" cy="32" r="6" fill="none" stroke="#e57c22" stroke-width="4"/><circle cx="42" cy="15" r="7" fill="none" stroke="#e57c22" stroke-width="6" stroke-dasharray="3.5 2.5"/><circle cx="42" cy="15" r="3" fill="none" stroke="#e57c22" stroke-width="3"/></svg>
  <h3>MAINTENANCE</h3>
  <p class="body-text">Lorem Ipsum is simply dummy text of the printing and typesetting industry. Lorem Ipsum has been the industry.</p>
</div>

<div class="abs why-band"></div>
<section class="why">
  <h2 style="left:79px">Why Kavreo E-Commerce ?</h2>
  <div class="why-mark" style="left:68px">Kavreo</div>
  <div class="why-rule" style="left:226px"></div>
  <p class="why-text body-text" style="left:251px">Lorem Ipsum is simply dummy text of the printing and typesetting industry. Lorem Ipsum has been the industry's standard dummy text ever since the 1500.</p>
  <a class="btn" href="#" style="left:251px;top:1537px;width:181px">Contact Us</a>
</section>
<section class="why">
  <h2 style="left:651px">Why Torvista ?</h2>
  <div class="why-mark" style="left:646px">Torvista</div>
  <div class="why-rule" style="left:798px"></div>
  <p class="why-text body-text" style="left:823px">Lorem Ipsum is simply dummy text of the printing and typesetting industry. Lorem Ipsum has been the industry's standard dummy text ever since the 1500.</p>
  <a class="btn" href="#" style="left:823px;top:1537px;width:167px">Read More</a>
</section>

<h2 class="abs section-title work-title"><span class="accent">Our</span> Work</h2>
<article class="abs work-card" style="left:77px">
  <div class="work-thumb">Ledgerhold</div>
  <h4>Ledgerhold</h4>
  <p class="body-text">Bravuln are prompt and get the job done with the highest level of workmanship at a resonable price.</p>
  <cite>Gavin Trelawny, Ledgerhold</cite>
</article>
<article class="abs work-card" style="left:348px">
  <div class="work-thumb">Plinto</div>
  <h4>Plinto</h4>
  <p class="body-text">A fast solution is key when you are selling online. Bravuln are now our go to Torvista developers, very happy.</p>
  <cite>Pieter Vandekamp, Plinto</cite>
</article>
<article class="abs work-card" style="left:617px">
  <div class="work-thumb">Sorelle</div>
  <h4>Sorelle</h4>
  <p class="body-text">Bravuln went above and beyond by delivering great work in excellent time frames.</p>
  <cite>Cormac Ashby, Sorelle</cite>
</article>
<article class="abs work-card" style="left:889px">
  <div class="work-thumb">Velmira</div>
  <h4>Ledgerhold</h4>
  <p class="body-text">Bravuln are great developers whose concentration on detail does not compromise the delivery of work.</p>
  <cite>Rowan Ellery, Velmira Lingerie</cite>
</article>

<section>
  <div class="abs newsletter" role="img" aria-label="Dark photo of hands typing on a laptop keyboard"></div>
  <h2 class="abs newsletter-title">NEWSLETTER</h2>
  <p class="abs newsletter-sub">Subscribe to Torvista Support and Security Updates</p>
  <div class="field" style="left:163px">Enter Name</div>
  <div class="field" style="left:517px">Enter Emaill</div>
  <a class="btn btn-subscribe" href="#">Subscribe</a>
</section>

<footer>
  <span class="partner" style="left:163px">Torvista</span>
  <span class="partner" style="left:435px">DataVane</span>
  <span class="partner" style="left:646px">QRX</span>
  <span class="partner" style="left:875px">NCB</span>
  <p class="abs copyright">© <strong>Kavreo E-commerce</strong> - 2016. All Rights Reserved.</p>
</footer>

</body>
</html>
```